Building company buisness cards

We are looking for a sharp modern new look for our business cards.
We are a New Zealand based company that specialises in house and land packages.
We have attached a photo of the current logo and would like to see if it can be improved somehow if needed.
We are open to any colours but we have chosen green at this stage.
Feel free to change the font and make the logo smarter looking.
Play with the colours and see what looks best.

We want a card that looks so good know one will want to throw it away!

Target Market(s)

Home buyers

Industry/Entity Type

Building

Contact Information for Business Card

Derek Tolvane
0217394062
dtolvane@quillmarkhomesteads.co.nz
quillmarkhomesteads.co.nz

Font styles to use
Serif
Sans Serif

Colors

Designer to choose colors to be used in the design.

Requirements
Must have
• Logo and company name on one side, details on the other side
Nice to have
• Color codes for the original green are HEX #4a8028, RGB(74,128,40), CMYK(42,0,69,50)
• Round corners, Raised and/or spot UV

```html
<!DOCTYPE html>
<html lang="en">
<head>
<meta charset="utf-8">
<title>Quillmark Homesteads – Business Card</title>
<link href="https://fonts.googleapis.com/css2?family=Montserrat:wght@400;700;800&display=swap" rel="stylesheet">
<style>
  :root {
    --brand-green: #4a8028;
    --card-black: #1b1b1b;
    --card-white: #ffffff;
    --wave-grey: #b3b3b3;
    --text-dark: #2a2a2a;
    --backdrop: #3a3a3a;
  }
  * { margin: 0; padding: 0; box-sizing: border-box; }
  html, body {
    width: 1200px;
    height: 900px;
    overflow: hidden;
    background: var(--backdrop);
    font-family: "Montserrat", sans-serif;
  }
  .canvas {
    position: relative;
    width: 1200px;
    height: 900px;
  }
  .card {
    position: absolute;
    left: 250px;
    width: 700px;
    height: 400px;
    border-radius: 24px;
    overflow: hidden;
    box-shadow: 0 10px 30px rgba(0,0,0,0.35);
  }
  .card--back {
    top: 35px;
    background: var(--card-black);
    display: flex;
    align-items: center;
    justify-content: center;
  }
  .card--front {
    top: 465px;
    background: var(--card-white);
  }
  .brand-name {
    color: var(--brand-green);
    font-weight: 800;
    line-height: 0.95;
    letter-spacing: -0.5px;
    text-align: center;
  }
  .card--back .brand-name { font-size: 64px; }
  .card--front .brand-name {
    position: absolute;
    right: 50px;
    top: 40px;
    font-size: 40px;
  }
  .holder {
    position: absolute;
    left: 48px;
    top: 46px;
  }
  .holder__name {
    color: var(--brand-green);
    font-weight: 700;
    font-size: 24px;
  }
  .holder__title {
    color: var(--text-dark);
    font-weight: 400;
    font-size: 18px;
    margin-top: 2px;
  }
  .divider {
    position: absolute;
    left: 48px;
    right: 40px;
    top: 140px;
    height: 3px;
    background: var(--brand-green);
  }
  .contact {
    position: absolute;
    left: 48px;
    top: 168px;
    list-style: none;
  }
  .contact__item {
    display: flex;
    align-items: center;
    gap: 8px;
    color: var(--text-dark);
    font-size: 18px;
    line-height: 25px;
  }
  .contact__icon { width: 13px; height: 13px; flex: none; }
  .wave {
    position: absolute;
    left: 0;
    bottom: 0;
    width: 700px;
    height: 400px;
  }
</style>
</head>
<body>
<main class="canvas">
  <section class="card card--back">
    <p class="brand-name">Quillmark<br>Homesteads.</p>
  </section>

  <section class="card card--front">
    <svg class="wave" viewBox="0 0 700 400" aria-hidden="true">
      <path d="M0,280 C130,262 230,300 340,345 C450,385 570,394 700,392 L700,400 L0,400 Z" fill="var(--wave-grey)"/>
      <path d="M0,292 C130,276 225,312 330,356 C440,398 560,404 700,404 L700,400 L0,400 Z" fill="var(--brand-green)"/>
    </svg>

    <div class="holder">
      <h1 class="holder__name">Derek Tolvane</h1>
      <p class="holder__title">Founder</p>
    </div>

    <div class="divider"></div>

    <p class="brand-name">Quillmark<br>Homesteads.</p>

    <ul class="contact">
      <li class="contact__item">
        <svg class="contact__icon" viewBox="0 0 16 16" aria-hidden="true"><path d="M4 1 L6.5 4.5 L5 6.2 C6 8.5 7.5 10 9.8 11 L11.5 9.5 L15 12 L13.5 15 C7 14.5 1.5 9 1 2.5 Z" fill="var(--brand-green)"/></svg>
        0217394062
      </li>
      <li class="contact__item">
        <svg class="contact__icon" viewBox="0 0 16 16" aria-hidden="true"><rect x="1" y="3" width="14" height="10" rx="1" fill="none" stroke="var(--brand-green)" stroke-width="1.6"/><path d="M1.5 3.5 L8 9 L14.5 3.5" fill="none" stroke="var(--brand-green)" stroke-width="1.6"/></svg>
        dtolvane@quillmarkhomesteads.co.nz
      </li>
      <li class="contact__item">
        <svg class="contact__icon" viewBox="0 0 16 16" aria-hidden="true"><circle cx="8" cy="8" r="7" fill="none" stroke="var(--brand-green)" stroke-width="1.6"/><ellipse cx="8" cy="8" rx="3" ry="7" fill="none" stroke="var(--brand-green)" stroke-width="1.3"/><path d="M1 8 H15" stroke="var(--brand-green)" stroke-width="1.3"/></svg>
        quillmarkhomesteads.co.nz
      </li>
    </ul>
  </section>
</main>
</body>
</html>
```